Create a business promotion flyer to leave in customer mailboxes. We are a bulk petroleum supplier, servicing any industry that requires diesel. Base in griffith NSW, servicing griffith area and surrounds.

Business Name - Terra Diesel
Fuel@terradiesel-example.com.au
Owen - 0491 570 362 ohartley@terradiesel-example.com.au
Liam - 0491 570 718 lprosser@terradiesel-example.com.au
Simon - 0491 570 905 skenway@terradiesel-example.com.au
Office 02 5550 1734

Bulk Fuel deliveries.
Oils & lubricants
Local Family owned business

```html
<!DOCTYPE html>
<html lang="en">
<head>
<meta charset="utf-8">
<title>Terra Diesel – Bulk Fuel Deliveries</title>
<link rel="stylesheet" href="https://fonts.googleapis.com/css2?family=Poppins:wght@400;500;600;800&family=Barlow+Semi+Condensed:wght@600;700&display=swap">
<style>
  :root {
    --red: #ee2b24;
    --grey: #5f5f61;
    --ink: #2b2b2d;
    --black: #232323;
    --white: #ffffff;
    --paper: #ebe9e6;
    --sky-top: #8fd0ee;
    --sky-low: #e9f5fb;
    --concrete: #cfcdca;
  }
  * { margin: 0; padding: 0; box-sizing: border-box; }
  html, body { width: 980px; height: 1200px; overflow: hidden; }
  body { font-family: "Poppins", sans-serif; background: var(--paper); }

  .flyer { position: relative; width: 980px; height: 1200px; overflow: hidden; }

  .backdrop {
    position: absolute; inset: 0;
    background: linear-gradient(180deg, var(--sky-top) 0%, var(--sky-low) 28%, #f4f8fa 40%, var(--concrete) 60%, #dddbd8 78%, var(--paper) 100%);
  }
  .depot-photo {
    position: absolute; left: 0; top: 358px; width: 980px; height: 330px;
    background: linear-gradient(180deg, #b9c0c6 0%, #8d949a 30%, #f2f2f2 50%, #dcdcdc 70%, #c9c7c4 100%);
  }

  .swooshes { position: absolute; inset: 0; }

  .brand-mark {
    position: absolute; top: 112px; left: 0; width: 980px;
    display: flex; justify-content: center; align-items: center; gap: 12px;
  }
  .brand-mark .dot { width: 26px; height: 26px; border-radius: 50%; background: var(--red); }
  .brand-mark .name { font-size: 42px; font-weight: 500; color: var(--grey); letter-spacing: 0.5px; }

  .headline {
    position: absolute; top: 188px; left: 0; width: 980px; text-align: center;
    font-size: 80px; font-weight: 800; letter-spacing: -1px; line-height: 110px;
  }
  .headline .first { color: var(--red); }
  .headline .second { color: var(--grey); }

  .tagline {
    position: absolute; top: 304px; left: 153px; width: 688px; height: 36px;
    background: var(--black); color: var(--white);
    clip-path: polygon(0 0, 100% 0, 97% 50%, 100% 100%, 0 100%, 3% 50%);
    font-size: 20px; font-weight: 500; letter-spacing: 3.4px;
    display: flex; align-items: center; justify-content: center;
  }

  .service-title { position: absolute; left: 72px; top: 664px; line-height: 1; }
  .service-title .lead { display: block; color: var(--red); font-size: 44px; font-weight: 800; letter-spacing: -0.5px; }
  .service-title .main { display: block; color: var(--ink); font-size: 56px; font-weight: 800; letter-spacing: -1px; margin-top: 4px; }

  .service-list { position: absolute; left: 72px; top: 783px; list-style: none; }
  .service-list li { display: flex; align-items: center; gap: 10px; height: 42px; margin-bottom: 7px; font-size: 21px; font-weight: 500; color: var(--ink); }
  .service-list svg { width: 36px; height: 36px; flex: none; }

  .base-badge { position: absolute; left: 633px; top: 578px; width: 286px; height: 286px; }
  .base-badge .map {
    position: absolute; inset: 12px; border-radius: 50%;
    background: radial-gradient(circle at 50% 45%, #f2f1f0 0%, #e2e0de 70%, #d4d2cf 100%);
  }
  .base-badge .ring { position: absolute; inset: 0; }
  .base-badge .text { position: absolute; top: 54px; width: 100%; text-align: center; font-family: "Barlow Semi Condensed", sans-serif; font-weight: 700; line-height: 1; }
  .base-badge .small { display: block; color: var(--red); font-size: 28px; }
  .base-badge .city { display: block; color: var(--red); font-size: 46px; margin-top: 2px; }
  .base-badge .state { display: block; color: var(--grey); font-size: 38px; margin-top: 2px; }
  .base-badge .pin { position: absolute; left: 126px; top: 190px; width: 34px; height: 46px; }

  .coverage-band {
    position: absolute; left: 537px; top: 812px; width: 443px; height: 107px;
    background: var(--red); border-radius: 54px 0 0 54px;
    display: flex; align-items: center;
  }
  .coverage-band .icon {
    width: 86px; height: 86px; border-radius: 50%; background: var(--white); margin-left: 10px;
    display: flex; align-items: center; justify-content: center; flex: none;
  }
  .coverage-band .label {
    margin-left: 14px; color: var(--white); font-family: "Barlow Semi Condensed", sans-serif;
    font-weight: 700; font-size: 27px; line-height: 32px; letter-spacing: 0.6px;
  }

  .contact-card { position: absolute; top: 990px; width: 284px; height: 107px; text-align: center; }
  .contact-card .plate {
    position: absolute; inset: 0; clip-path: polygon(24px 0, 100% 0, 100% 80px, 257px 100%, 0 100%, 0 24px);
  }
  .contact-card.red .plate { background: var(--red); }
  .contact-card.grey .plate { background: var(--grey); }
  .contact-card .call {
    position: absolute; left: 106px; top: -36px; width: 72px; height: 72px; border-radius: 50%;
    border: 4px solid #d9d6d2; display: flex; align-items: center; justify-content: center;
  }
  .contact-card.red .call { background: var(--grey); }
  .contact-card.grey .call { background: var(--red); }
  .contact-card .person { position: absolute; top: 44px; width: 100%; color: var(--white); font-size: 23px; font-weight: 400; letter-spacing: 0.5px; }
  .contact-card .phone { position: absolute; top: 70px; width: 100%; color: var(--white); font-size: 25px; font-weight: 800; letter-spacing: 0.5px; }

  .email-line {
    position: absolute; top: 1128px; left: 0; width: 980px;
    display: flex; align-items: center; justify-content: center; gap: 10px;
  }
  .email-line .rule { width: 48px; height: 2px; background: var(--red); }
  .email-line .address { font-size: 20px; font-weight: 600; color: var(--black); letter-spacing: 3px; text-transform: uppercase; }
</style>
</head>
<body>
<main class="flyer">
  <div class="backdrop" role="img" aria-label="Photo background: blue sky with white clouds fading into a light concrete yard"></div>
  <div class="depot-photo" role="img" aria-label="Photo: white fuel tanker road train parked in front of a large steel warehouse"></div>

  <svg class="swooshes" viewBox="0 0 980 1200" width="980" height="1200" aria-hidden="true">
    <path d="M0,0 H432 C250,20 95,120 0,230 Z" fill="#ee2b24"/>
    <path d="M55,145 C150,50 290,8 432,0 C300,20 170,70 55,145 Z" fill="#5f5f61"/>
    <path d="M980,326 C955,400 900,452 822,480 L980,480 Z" fill="#ee2b24"/>
    <path d="M938,376 C900,420 860,448 806,466 C860,440 905,410 938,376 Z" fill="#5f5f61"/>
  </svg>

  <div class="brand-mark">
    <span class="dot"></span>
    <span class="name">Terra Diesel</span>
  </div>

  <h1 class="headline"><span class="first">TERRA</span> <span class="second">DIESEL</span></h1>
  <p class="tagline">RELIABLE. LOCAL. READY TO DELIVER</p>

  <h2 class="service-title"><span class="lead">BULK FUEL</span><span class="main">DELIVERIES</span></h2>

  <ul class="service-list">
    <li>
      <svg viewBox="0 0 36 36"><circle cx="18" cy="18" r="17" fill="#ee2b24"/><path d="M18 9 C14 15 12 18 12 21 a6 6 0 0 0 12 0 C24 18 22 15 18 9 Z" fill="none" stroke="#fff" stroke-width="1.8"/></svg>
      Oils &amp; lubricants
    </li>
    <li>
      <svg viewBox="0 0 36 36"><circle cx="18" cy="18" r="17" fill="#ee2b24"/><rect x="8" y="12" width="13" height="10" fill="none" stroke="#fff" stroke-width="1.6"/><path d="M21 15 h4 l3 4 v3 h-7" fill="none" stroke="#fff" stroke-width="1.6"/><circle cx="12" cy="24" r="2" fill="#fff"/><circle cx="24" cy="24" r="2" fill="#fff"/></svg>
      Petrol deliveries
    </li>
    <li>
      <svg viewBox="0 0 36 36"><circle cx="18" cy="18" r="17" fill="#ee2b24"/><circle cx="18" cy="18" r="12" fill="none" stroke="#fff" stroke-width="1.2"/><path d="M11 19 L18 12 L25 19 M13 18 V25 H23 V18" fill="none" stroke="#fff" stroke-width="1.6"/></svg>
      Local Family owned business
    </li>
  </ul>

  <div class="base-badge">
    <div class="map" role="img" aria-label="Map of south-west New South Wales around Griffith"></div>
    <svg class="ring" viewBox="0 0 286 286" aria-hidden="true">
      <circle cx="143" cy="143" r="137" fill="none" stroke="#5f5f61" stroke-width="7"/>
      <path d="M18,95 A137,137 0 0 1 268,95" fill="none" stroke="#ee2b24" stroke-width="7"/>
    </svg>
    <p class="text"><span class="small">BASED IN</span><span class="city">GRIFFITH</span><span class="state">NSW</span></p>
    <svg class="pin" viewBox="0 0 34 46" aria-hidden="true"><path d="M17 0 a17 17 0 0 1 17 17 C34 29 17 46 17 46 S0 29 0 17 A17 17 0 0 1 17 0 Z" fill="#ee2b24"/><circle cx="17" cy="17" r="7" fill="#fff"/></svg>
  </div>

  <div class="coverage-band">
    <div class="icon">
      <svg width="60" height="36" viewBox="0 0 60 36" aria-hidden="true"><rect x="16" y="3" width="42" height="24" fill="none" stroke="#333" stroke-width="2.4"/><path d="M16 12 H8 L3 20 V27 H16" fill="none" stroke="#333" stroke-width="2.4"/><circle cx="10" cy="30" r="4" fill="#fff" stroke="#333" stroke-width="2.4"/><circle cx="40" cy="30" r="4" fill="#fff" stroke="#333" stroke-width="2.4"/><circle cx="50" cy="30" r="4" fill="#fff" stroke="#333" stroke-width="2.4"/></svg>
    </div>
    <p class="label">SERVICING GRIFFITH<br>AREA &amp; SURROUNDS</p>
  </div>

  <div class="contact-card red" style="left:54px">
    <div class="plate"></div>
    <div class="call"><svg width="36" height="36" viewBox="0 0 36 36" aria-hidden="true"><path d="M10 5 l5 6 -3 4 c2 4 5 7 9 9 l4-3 6 5 -3 5 c-10 0 -22 -12 -22 -22 Z" fill="none" stroke="#fff" stroke-width="2"/><path d="M21 6 a9 9 0 0 1 9 9 M21 11 a4 4 0 0 1 4 4" fill="none" stroke="#fff" stroke-width="2"/></svg></div>
    <p class="person">OWEN</p>
    <p class="phone">0491 570 362</p>
  </div>

  <div class="contact-card grey" style="left:351px">
    <div class="plate"></div>
    <div class="call"><svg width="36" height="36" viewBox="0 0 36 36" aria-hidden="true"><path d="M10 5 l5 6 -3 4 c2 4 5 7 9 9 l4-3 6 5 -3 5 c-10 0 -22 -12 -22 -22 Z" fill="none" stroke="#fff" stroke-width="2"/><path d="M21 6 a9 9 0 0 1 9 9 M21 11 a4 4 0 0 1 4 4" fill="none" stroke="#fff" stroke-width="2"/></svg></div>
    <p class="person">LIAM</p>
    <p class="phone">0491 570 718</p>
  </div>

  <div class="contact-card red" style="left:649px">
    <div class="plate"></div>
    <div class="call"><svg width="36" height="36" viewBox="0 0 36 36" aria-hidden="true"><path d="M10 5 l5 6 -3 4 c2 4 5 7 9 9 l4-3 6 5 -3 5 c-10 0 -22 -12 -22 -22 Z" fill="none" stroke="#fff" stroke-width="2"/><path d="M21 6 a9 9 0 0 1 9 9 M21 11 a4 4 0 0 1 4 4" fill="none" stroke="#fff" stroke-width="2"/></svg></div>
    <p class="person">SIMON</p>
    <p class="phone">0491 570 905</p>
  </div>

  <div class="email-line">
    <span class="rule"></span>
    <span class="address">Fuel@terradiesel-example.com.au</span>
    <span class="rule"></span>
  </div>
</main>
</body>
</html>
```